Business cards and stationary design

We just completed the design of our new logo and we need to print new business cards and letterhead for our nonprofit. We are looking for a fresh new design that shows off our new logo. On letterhead, we must have a column on the right or left to include our Board of Directors (up to 45 names) (see attachment)

Industry/Entity Type

Non-Profit

Contact Information for Business Card

Standard business card with name, title, Company name, mailing address phone numbers, email address and website. Tagline on back "Bringing the homeless home"

Font styles to use
Sans Serif

Requirements
Must have
• include pertinent information above
• new logo
• fonts compatible with logo
• should use logo colors only
Nice to have
• tag lines

```html
<!DOCTYPE html>
<html lang="en">
<head>
<meta charset="utf-8">
<title>Homeward Shelter Network — Business Card</title>
<link rel="stylesheet" href="https://fonts.googleapis.com/css2?family=Roboto:wght@400;700&family=Michroma&display=swap">
<style>
  :root {
    --bg: #2a2a2a;
    --brand-red: #d62027;
    --brand-teal: #0383a3;
    --card-white: #f2f2f2;
    --text-light: #ffffff;
  }
  * { margin: 0; padding: 0; box-sizing: border-box; }
  html, body {
    width: 1200px; height: 960px; overflow: hidden;
    background: var(--bg);
  }
  .canvas { position: relative; width: 1200px; height: 960px; }

  .card {
    position: absolute; left: 320px; width: 600px; height: 345px;
    overflow: hidden;
  }

  /* Front */
  .card-front { top: 100px; background: var(--brand-red); }
  .front-brand {
    position: absolute; left: 0; right: 0; top: 150px;
    display: flex; align-items: center; justify-content: center; gap: 14px;
    font-family: "Michroma", sans-serif; font-size: 24px;
    color: var(--text-light); letter-spacing: 2px;
  }
  .front-brand .mark { width: 18px; height: 18px; border-radius: 50%; background: var(--text-light); }
  .front-web {
    position: absolute; left: 0; right: 0; top: 300px; text-align: center;
    font-family: "Roboto", sans-serif; font-size: 15px;
    color: var(--text-light); letter-spacing: 6px;
  }

  /* Back */
  .card-back { top: 493px; height: 342px; background: var(--card-white); }
  .back-brand {
    position: absolute; left: 0; right: 0; top: 90px;
    display: flex; align-items: center; justify-content: center; gap: 10px;
    font-family: "Michroma", sans-serif; font-size: 17px;
    color: var(--brand-teal); letter-spacing: 1.5px;
  }
  .back-brand .mark { width: 12px; height: 12px; border-radius: 50%; background: var(--brand-teal); }
  .back-bands { position: absolute; left: 0; top: 0; width: 600px; height: 342px; }
  .contact {
    position: absolute; left: 0; right: 0; top: 236px; text-align: center;
    font-family: "Roboto", sans-serif; font-weight: 700; color: var(--text-light);
  }
  .contact-name { font-size: 20px; line-height: 26px; }
  .contact-title { font-size: 14px; margin-left: 4px; }
  .contact-line { font-size: 13.5px; line-height: 22px; }
  .contact-web { font-size: 13px; line-height: 18px; }
</style>
</head>
<body>
<main class="canvas">
  <section class="card card-front">
    <div class="front-brand"><span class="mark"></span>Homeward Shelter Network</div>
    <p class="front-web">www.homewardnetwork.org</p>
  </section>

  <section class="card card-back">
    <div class="back-brand"><span class="mark"></span>Homeward Shelter Network</div>
    <svg class="back-bands" viewBox="0 0 600 342" aria-hidden="true">
      <path d="M0,292 C60,205 200,166 330,168 C450,172 555,228 600,296 L600,342 L0,342 Z" fill="var(--brand-red)"/>
      <path d="M0,308 C70,240 200,200 320,200 C440,200 545,240 600,300 L600,342 L0,342 Z" fill="var(--brand-teal)" stroke="#ffffff" stroke-width="2"/>
    </svg>
    <div class="contact">
      <p class="contact-name">DANIEL REYES - <span class="contact-title">CEO/FOUNDER</span></p>
      <p class="contact-line">2140 Alder Court&nbsp; Fairbanks, Alaska 99701</p>
      <p class="contact-line">P. 555 014 2290&nbsp; E. daniel@homewardnetwork.org</p>
      <p class="contact-web">www.homewardnetwork.org</p>
    </div>
  </section>
</main>
</body>
</html>
```